RESIDENTIAL CONSTRUCTION

We are a company that specializes in building custom residential homes, the design should also emphasize that quality and service is our priority.

Industry/Entity Type

Construction Company

Contact Information for Business Card

Contact Person: Marcus Lindqvist
Company Address: 273 West Alder Ave San Jose , Ca 95380
Phone Number : 408-731-2946
Email Address: Stoneridgehomes517@mailvista.net

Font styles to use
Sans Serif

Colors
ec1f27

Requirements
Must have
• CSLB # 7362015
Nice to have
• needs to have same color as logo i uploaded, we will be printing these on a clear plastic card.

```html
<!DOCTYPE html>
<html lang="en">
<head>
<meta charset="utf-8">
<title>Stoneridge General Builders – Business Card</title>
<link href="https://fonts.googleapis.com/css2?family=Oswald:wght@500&family=Open+Sans:wght@400&display=swap" rel="stylesheet">
<style>
  :root {
    --bg: #2a2a2a;
    --card: #1d1d1d;
    --white: #f2f2f2;
    --silver: #b9b9b9;
    --red: #ec1f27;
    --text-muted: #e6e6e6;
  }
  * { margin: 0; padding: 0; box-sizing: border-box; }
  html, body { width: 1200px; height: 900px; overflow: hidden; background: var(--bg); }
  .canvas { position: relative; width: 1200px; height: 900px; }
  .card {
    position: absolute; left: 250px; width: 700px; height: 400px;
    background: var(--card); border-radius: 3px;
  }
  .card--front { top: 35px; }
  .card--back { top: 465px; }

  .logo { position: absolute; display: flex; align-items: center; gap: 14px; font-family: "Oswald", sans-serif; font-weight: 500; }
  .logo__mark { width: 22px; height: 22px; flex: none; }
  .logo__name { display: flex; flex-direction: column; line-height: 1; text-transform: uppercase; }
  .logo__main { font-size: 62px; letter-spacing: 1px; }
  .logo__sub { font-size: 19px; letter-spacing: 7px; margin-top: 4px; }

  .card--front .logo { left: 50%; top: 50%; transform: translate(-50%, -50%); color: var(--silver); }
  .card--front .logo__mark { background: var(--silver); }

  .card--back .logo { right: 48px; top: 110px; color: var(--red); }
  .card--back .logo__main { font-size: 40px; }
  .card--back .logo__sub { font-size: 12px; letter-spacing: 4.5px; margin-top: 3px; }
  .card--back .logo__mark { width: 16px; height: 16px; background: var(--red); }

  .person { position: absolute; left: 52px; top: 46px; font-family: "Oswald", sans-serif; font-weight: 500; text-transform: uppercase; }
  .person__name { color: var(--white); font-size: 28px; letter-spacing: 0.5px; line-height: 1.1; }
  .person__title { color: var(--red); font-size: 17px; letter-spacing: 0.5px; margin-top: 2px; }
  .person__rule { width: 72px; height: 3px; background: var(--red); margin-top: 10px; }

  .contact { position: absolute; left: 52px; bottom: 52px; list-style: none; font-family: "Open Sans", sans-serif; font-size: 18px; color: var(--text-muted); }
  .contact__item { display: flex; align-items: center; gap: 12px; line-height: 1.55; }
  .contact__icon { width: 16px; height: 16px; flex: none; fill: var(--red); }
</style>
</head>
<body>
<main class="canvas">
  <section class="card card--front" aria-label="Card front">
    <div class="logo">
      <span class="logo__mark"></span>
      <span class="logo__name">
        <span class="logo__main">Stoneridge</span>
        <span class="logo__sub">General Builders</span>
      </span>
    </div>
  </section>

  <section class="card card--back" aria-label="Card back">
    <div class="person">
      <h1 class="person__name">Marcus Lindqvist</h1>
      <p class="person__title">Job Title | CSLB # 7362015</p>
      <div class="person__rule"></div>
    </div>

    <div class="logo">
      <span class="logo__mark"></span>
      <span class="logo__name">
        <span class="logo__main">Stoneridge</span>
        <span class="logo__sub">General Builders</span>
      </span>
    </div>

    <ul class="contact">
      <li class="contact__item">
        <svg class="contact__icon" viewBox="0 0 24 24" aria-hidden="true"><path d="M6.6 10.8a15.1 15.1 0 0 0 6.6 6.6l2.2-2.2a1 1 0 0 1 1-.25 11.4 11.4 0 0 0 3.6.57 1 1 0 0 1 1 1V20a1 1 0 0 1-1 1A17 17 0 0 1 3 4a1 1 0 0 1 1-1h3.5a1 1 0 0 1 1 1c0 1.25.2 2.45.57 3.57a1 1 0 0 1-.25 1z"/></svg>
        <span>408-731-2946</span>
      </li>
      <li class="contact__item">
        <svg class="contact__icon" viewBox="0 0 24 24" aria-hidden="true"><path d="M2 5h20v14H2z M3.5 6.5 12 13l8.5-6.5" stroke="#1d1d1d" stroke-width="1.5"/></svg>
        <span>Stoneridgehomes517@mailvista.net</span>
      </li>
      <li class="contact__item">
        <svg class="contact__icon" viewBox="0 0 24 24" aria-hidden="true"><path d="M12 2a7 7 0 0 0-7 7c0 5.2 7 13 7 13s7-7.8 7-13a7 7 0 0 0-7-7zm0 9.5A2.5 2.5 0 1 1 12 6.5a2.5 2.5 0 0 1 0 5z"/></svg>
        <span>273 West Alder Ave San Jose , Ca 95380</span>
      </li>
    </ul>
  </section>
</main>
</body>
</html>
```